Transport & Storage Company needs a revamp of current card

Would like to keep same colours & basic design but would like to "sharpen" up look of card.

Please remove "The Brisk Haulers"

Please add 1800 418 239 on front & back of card

Please add email address on back of card - colin@bluegatefreight.com.au

I would like our ABN No - 38 214 906 731 on back of card (which currently has logo only). Logo on back of card can be removed if insufficient space.

Please design another card (same as above) but with Maren Ashcombe - 0431 702 548, maren@bluegatefreight.com.au

I do not want cards to look "too busy" so please re-arrange layout of card if necessary.

Target Market(s)

Transport & Storage

Industry/Entity Type

It Company

Contact Information for Business Card

Please refer to attached current business card

Font styles to use
Other font styles liked:
• Tahoma

Requirements
Must have
• Refer to project decsription
Nice to have
Should not have

```html
<!DOCTYPE html>
<html lang="en">
<head>
<meta charset="utf-8">
<title>Bluegate Freight – Business Cards</title>
<link rel="stylesheet" href="https://fonts.googleapis.com/css2?family=Open+Sans:wght@400;600;700&display=swap">
<style>
  :root {
    --purple: #7b3a90;
    --grey: #58595b;
    --ink: #2b2b2b;
    --paper: #ffffff;
    --backdrop: #e9e8ea;
  }
  * { margin: 0; padding: 0; box-sizing: border-box; }
  html, body { width: 1200px; height: 892px; overflow: hidden; }
  body {
    background: var(--backdrop);
    font-family: "Open Sans", Tahoma, sans-serif;
    color: var(--ink);
    display: flex;
    align-items: center;
    justify-content: center;
    gap: 40px;
  }
  .card {
    position: relative;
    width: 540px;
    height: 330px;
    background: var(--paper);
    box-shadow: 0 6px 18px rgba(0,0,0,0.18);
    overflow: hidden;
  }
  .card__stripes { position: absolute; inset: 0; width: 100%; height: 100%; }
  .brand {
    display: flex;
    align-items: center;
    gap: 10px;
  }
  .brand__dot {
    width: 26px; height: 26px;
    border-radius: 50%;
    background: var(--purple);
  }
  .brand__name {
    font-size: 26px;
    font-weight: 700;
    color: var(--purple);
    letter-spacing: 0.5px;
  }

  /* Front card */
  .card--front .card__content {
    position: absolute;
    left: 64px; top: 72px;
    width: 380px;
    text-align: center;
    display: flex;
    flex-direction: column;
    align-items: center;
  }
  .abn {
    margin-top: 8px;
    font-size: 11px;
    color: var(--purple);
    letter-spacing: 0.3px;
  }
  .front-phone {
    margin-top: 34px;
    font-size: 24px;
    color: var(--purple);
  }
  .website {
    margin-top: 10px;
    font-size: 21px;
    color: var(--purple);
  }

  /* Back card */
  .card--back .card__content {
    position: absolute;
    right: 40px; top: 30px;
    width: 390px;
    display: flex;
    flex-direction: column;
    align-items: flex-end;
  }
  .person {
    align-self: center;
    margin-top: 28px;
    font-size: 20px;
    font-weight: 700;
    color: var(--purple);
  }
  .email {
    align-self: center;
    margin-top: 16px;
    font-size: 16px;
    color: var(--ink);
  }
  .phones {
    margin-top: 40px;
    text-align: right;
    font-size: 18px;
    line-height: 1.4;
    color: var(--ink);
    letter-spacing: 0.5px;
  }
</style>
</head>
<body>

  <section class="card card--front" aria-label="Business card front">
    <svg class="card__stripes" viewBox="0 0 540 330" aria-hidden="true">
      <rect x="0" y="0" width="6" height="330" fill="var(--purple)"/>
      <polygon points="438,0 462,0 512,330 486,330" fill="var(--grey)"/>
      <polygon points="476,0 510,0 540,120 540,330 526,330" fill="var(--purple)"/>
    </svg>
    <div class="card__content">
      <div class="brand">
        <span class="brand__dot"></span>
        <span class="brand__name">Bluegate Freight</span>
      </div>
      <p class="abn">ABN No. 38 214 906 731</p>
      <p class="front-phone">1800 418 239</p>
      <p class="website">www.bluegatefreight.com.au</p>
    </div>
  </section>

  <section class="card card--back" aria-label="Business card back">
    <svg class="card__stripes" viewBox="0 0 540 330" aria-hidden="true">
      <polygon points="0,0 30,0 80,330 0,330" fill="var(--purple)"/>
      <polygon points="44,0 70,0 122,330 94,330" fill="var(--grey)"/>
      <rect x="528" y="0" width="12" height="330" fill="var(--grey)"/>
    </svg>
    <div class="card__content">
      <div class="brand">
        <span class="brand__dot"></span>
        <span class="brand__name">Bluegate Freight</span>
      </div>
      <p class="person">Colin Draycott</p>
      <p class="email">colin@bluegatefreight.com.au</p>
      <p class="phones">0450 316 208<br>1800 418 239</p>
    </div>
  </section>

</body>
</html>
```